Building company buisness cards

We are looking for a sharp modern new look for our business cards.
We are a New Zealand based company that specialises in house and land packages.
We have attached a photo of the current logo and would like to see if it can be improved somehow if needed.
We are open to any colours but we have chosen green at this stage.
Feel free to change the font and make the logo smarter looking.
Play with the colours and see what looks best.

We want a card that looks so good know one will want to throw it away!

Target Market(s)

Home buyers

Industry/Entity Type

Building

Contact Information for Business Card

Derek Tolvane
0217394062
dtolvane@quillmarkhomesteads.co.nz
quillmarkhomesteads.co.nz

Font styles to use
Serif
Sans Serif

Colors

Designer to choose colors to be used in the design.

Requirements
Must have
• Logo and company name on one side, details on the other side
Nice to have
• Color codes for the original green are HEX #4a8028, RGB(74,128,40), CMYK(42,0,69,50)
• Round corners, Raised and/or spot UV

```html
<!DOCTYPE html>
<html lang="en">
<head>
<meta charset="utf-8">
<title>Quillmark Homesteads – Business Card</title>
<link rel="stylesheet" href="https://fonts.googleapis.com/css2?family=Nunito:wght@300;700;800&display=swap">
<style>
  :root {
    --backdrop: #1e1e20;
    --card-dark: #161617;
    --card-light: #ffffff;
    --brand-green: #4a8028;
    --brand-green-soft: #e6efe0;
    --brand-green-mid: #cfe0c4;
  }
  * { box-sizing: border-box; margin: 0; padding: 0; }
  html, body {
    width: 1200px; height: 900px; overflow: hidden;
    background: var(--backdrop);
    font-family: "Nunito", Arial, sans-serif;
  }
  .canvas {
    position: relative; width: 1200px; height: 900px;
    display: flex; flex-direction: column; align-items: center;
    justify-content: center; gap: 24px;
  }
  .card {
    position: relative; width: 700px; height: 400px;
    border-radius: 10px; overflow: hidden;
  }

  /* Front */
  .card--front { background: var(--card-dark); }
  .holder-name {
    position: absolute; left: 44px; top: 40px;
    font-size: 30px; color: var(--brand-green); letter-spacing: 0.2px;
  }
  .holder-name__first { font-weight: 300; }
  .holder-name__last { font-weight: 800; }
  .holder-name__rule {
    position: absolute; left: 42px; top: 84px;
    width: 96px; height: 3px; background: var(--brand-green);
  }
  .company-name {
    position: absolute; right: 46px; bottom: 54px;
    text-align: right; color: var(--brand-green);
    font-weight: 800; line-height: 0.95;
  }
  .company-name__top { font-size: 34px; display: block; margin-right: 70px; }
  .company-name__bottom { font-size: 50px; display: block; }

  /* Back */
  .card--back { background: var(--card-light); }
  .contact-list {
    position: absolute; left: 40px; top: 230px;
    list-style: none; display: flex; flex-direction: column; gap: 14px;
  }
  .contact-list__item {
    display: flex; align-items: center; gap: 10px;
    color: var(--brand-green); font-weight: 700; font-size: 19px;
  }
  .contact-list__icon { width: 18px; height: 18px; flex: none; }
  .brand-illustration {
    position: absolute; left: 430px; top: 110px;
    width: 240px; height: 246px;
    background: linear-gradient(180deg, var(--brand-green-soft), var(--brand-green-mid));
    border-radius: 4px;
  }
  .footer-band {
    position: absolute; left: 0; right: 0; bottom: 0;
    height: 44px; background: var(--brand-green);
  }
</style>
</head>
<body>
<main class="canvas">
  <section class="card card--front" aria-label="Card front">
    <h1 class="holder-name">
      <span class="holder-name__first">Derek</span>
      <span class="holder-name__last">Tolvane</span>
    </h1>
    <div class="holder-name__rule"></div>
    <p class="company-name">
      <span class="company-name__top">quillmark</span>
      <span class="company-name__bottom">homesteads.</span>
    </p>
  </section>

  <section class="card card--back" aria-label="Card back">
    <ul class="contact-list">
      <li class="contact-list__item">
        <svg class="contact-list__icon" viewBox="0 0 24 24" aria-hidden="true">
          <path fill="#4a8028" d="M6.6 10.8a15 15 0 0 0 6.6 6.6l2.2-2.2a1 1 0 0 1 1-.25 11.4 11.4 0 0 0 3.6.57 1 1 0 0 1 1 1V20a1 1 0 0 1-1 1A17 17 0 0 1 3 4a1 1 0 0 1 1-1h3.5a1 1 0 0 1 1 1c0 1.25.2 2.45.57 3.57a1 1 0 0 1-.25 1z"/>
        </svg>
        0217394062
      </li>
      <li class="contact-list__item">
        <svg class="contact-list__icon" viewBox="0 0 24 24" aria-hidden="true">
          <rect x="2" y="5" width="20" height="14" rx="1.5" fill="none" stroke="#4a8028" stroke-width="2.2"/>
          <path d="M3 6l9 7 9-7" fill="none" stroke="#4a8028" stroke-width="2.2"/>
        </svg>
        dtolvane@quillmarkhomesteads.co.nz
      </li>
      <li class="contact-list__item">
        <svg class="contact-list__icon" viewBox="0 0 24 24" aria-hidden="true">
          <g fill="none" stroke="#4a8028" stroke-width="1.8">
            <circle cx="12" cy="12" r="9.5"/>
            <ellipse cx="12" cy="12" rx="4" ry="9.5"/>
            <path d="M2.5 12h19M4 7h16M4 17h16"/>
          </g>
        </svg>
        quillmarkhomesteads.co.nz
      </li>
    </ul>
    <div class="brand-illustration" role="img" aria-label="Large green brand illustration of a family sheltered under a roof"></div>
    <div class="footer-band"></div>
  </section>
</main>
</body>
</html>
```